New Business Card Design for Manufacturing

We are an engineering/manufacturing company that offers Advanced machining/assembly/engineering services, as well as innovative products for the heavy duty engine cooling markets.

We are looking to get a new business card designed that is clean and modern looking, but still fits the wide range of technical/skilled work we do.

- We hope to use this design as the base for other design work in new Presentations, web, and print work.

Industry/Entity Type

Engineering

Contact Information for Business Card

Our preferred color of blue is (RGB) 22/71/159 but can vary slightly from that color. Our content will be our Logo and full company name (Vantrell Forge Works, Inc.), company address, name, job title, phone number with extension, cell number, fax number, website, and email address on the cards.
We'd like the full company name next to the logo, but we are open to other interpretations of that layout.
Preferably, we would like the back side to be clean with just our logo, and the front to contain all of the contact information.

Colors
2f74b4
0355a3
85abd2

Requirements
Must have
• - Logo, company name, needed content - We are open to interpretation beyond that.
• - Standard size business card.
• - Horizontal orientation.
• - Enough space for lengthy names / job titles (for example, a job title could read "Directory of Human Resources" or "V.P. of Governmental Affairs"). We need this to look clean, whether the title be short (CEO) or long (as described above).

```html
<!DOCTYPE html>
<html lang="en">
<head>
<meta charset="utf-8">
<title>Vantrell Forge Works – Business Card</title>
<link rel="stylesheet" href="https://fonts.googleapis.com/css2?family=Open+Sans:wght@400;600;700;800&family=Arimo:wght@700&display=swap">
<style>
  :root {
    --brand-blue: #0b55a3;
    --sky-blue: #4fb3e8;
    --mid-blue: #9cc3e8;
    --pale-blue: #d6e6f6;
    --name-blue: #2f9ad8;
    --ink: #333a40;
    --white: #ffffff;
    --backdrop: #e4e6e9;
  }
  html, body {
    margin: 0;
    width: 1200px;
    height: 1000px;
    overflow: hidden;
    background: var(--backdrop);
    font-family: "Open Sans", Arial, sans-serif;
  }
  .canvas {
    position: relative;
    width: 1200px;
    height: 1000px;
  }
  .card {
    position: absolute;
    width: 640px;
    height: 366px;
    overflow: hidden;
    box-shadow: 0 10px 28px rgba(0,0,0,0.18);
  }
  .card-front { left: 200px; top: 70px; background: var(--white); }
  .card-back  { left: 360px; top: 540px; background: var(--brand-blue); }

  .contact-band {
    position: absolute;
    left: 0; right: 0; bottom: 0;
    height: 140px;
    background: var(--brand-blue);
  }

  .address-band {
    position: absolute;
    left: 150px;
    right: 0;
    top: 176px;
    height: 54px;
    border-radius: 27px 0 0 27px;
    background: linear-gradient(90deg, var(--pale-blue) 0%, var(--mid-blue) 30%, var(--sky-blue) 60%, var(--mid-blue) 100%);
  }

  .company-name {
    position: absolute;
    left: 24px;
    top: 34px;
    margin: 0;
    font-family: "Arimo", Arial, sans-serif;
    font-weight: 700;
    font-size: 19px;
    line-height: 20px;
    color: var(--name-blue);
    text-transform: uppercase;
  }
  .company-name small { font-size: 8px; }

  .brand-mark {
    position: absolute;
    right: 24px;
    top: 20px;
    display: flex;
    align-items: center;
    gap: 6px;
    font-weight: 800;
    font-size: 17px;
    color: var(--brand-blue);
  }
  .brand-mark .square { width: 12px; height: 12px; background: var(--brand-blue); }

  .person {
    position: absolute;
    left: 0; right: 0;
    top: 104px;
    text-align: center;
    color: var(--ink);
  }
  .person-name { margin: 0; font-size: 22px; font-weight: 400; letter-spacing: 1px; }
  .person-title { margin: 4px 0 0; font-size: 12.5px; letter-spacing: 1px; }

  .address {
    position: absolute;
    left: 250px;
    top: 176px;
    height: 54px;
    display: flex;
    align-items: center;
    gap: 10px;
    color: var(--white);
    font-size: 13px;
    letter-spacing: 1px;
  }

  .contact-list {
    position: absolute;
    margin: 0;
    padding: 0;
    list-style: none;
    color: var(--white);
    font-size: 13px;
    letter-spacing: 1px;
  }
  .contact-list li { display: flex; align-items: center; gap: 10px; height: 24px; }
  .contact-list svg { width: 14px; height: 14px; fill: var(--white); }
  .contact-phones { left: 30px; top: 262px; }
  .contact-online { left: 380px; top: 244px; }

  .back-brand {
    position: absolute;
    left: 0; right: 0;
    top: 120px;
    display: flex;
    justify-content: center;
    align-items: center;
    gap: 14px;
    font-weight: 800;
    font-size: 48px;
    color: var(--white);
  }
  .back-brand .square { width: 30px; height: 30px; background: var(--white); }

  .web-tab {
    position: absolute;
    left: 300px;
    right: 40px;
    bottom: 0;
    height: 92px;
    background: var(--white);
    border-radius: 36px 36px 0 0;
    display: flex;
    justify-content: center;
    padding-top: 22px;
    box-sizing: border-box;
    color: var(--brand-blue);
    font-size: 17px;
  }
</style>
</head>
<body>
<main class="canvas">

  <section class="card card-front" aria-label="Business card front">
    <div class="contact-band"></div>
    <div class="address-band" role="img" aria-label="Decorative band of graded blue tabs behind the address"></div>

    <h1 class="company-name">Vantrell<br>Forge<br>Works <small>INC</small></h1>

    <div class="brand-mark"><span class="square"></span>Vantrell Forge</div>

    <div class="person">
      <p class="person-name">NAME OF CEO</p>
      <p class="person-title">DIRECTORY OF HUMAN RESOURCES</p>
    </div>

    <div class="address">
      <svg width="12" height="14" viewBox="0 0 12 14" aria-hidden="true"><path d="M6 0a5 5 0 0 0-5 5c0 4 5 9 5 9s5-5 5-9a5 5 0 0 0-5-5zm0 7a2 2 0 1 1 0-4 2 2 0 0 1 0 4z" fill="#fff"/></svg>
      YOUR COMPANY ADDRESS
    </div>

    <ul class="contact-list contact-phones">
      <li><svg viewBox="0 0 14 14" aria-hidden="true"><rect x="1" y="6" width="12" height="7" rx="1"/><path d="M0 5c2-4 12-4 14 0l-3 1-1-2H4L3 6z"/></svg>PHONE NUMBER</li>
      <li><svg viewBox="0 0 14 14" aria-hidden="true"><path d="M3 1l2 3-1 2c1 2 2 3 4 4l2-1 3 2-1 2C6 14 0 8 1 2z"/></svg>CELL NUMBER</li>
      <li><svg viewBox="0 0 14 14" aria-hidden="true"><rect x="3" y="0" width="8" height="4"/><rect x="0" y="4" width="14" height="6" rx="1"/><rect x="3" y="9" width="8" height="5"/></svg>FAX NUMBER</li>
    </ul>

    <ul class="contact-list contact-online">
      <li><svg viewBox="0 0 14 14" aria-hidden="true"><circle cx="7" cy="7" r="7"/></svg>WEBSITE</li>
      <li><svg viewBox="0 0 14 14" aria-hidden="true"><path d="M0 3h14v9H0z"/><path d="M0 3l7 5 7-5" fill="none" stroke="#0b55a3" stroke-width="1.2"/></svg>EMAIL ADDRESS</li>
    </ul>
  </section>

  <section class="card card-back" aria-label="Business card back">
    <div class="back-brand"><span class="square"></span>Vantrell Forge</div>
    <div class="web-tab">www.website.com</div>
  </section>

</main>
</body>
</html>
```